Dynamic Business Card for Sports Supplements Company

Hi! I'm looking for an awesome business card to match my existing sports supplement company. I have uploaded my current company logo and screenshot of the front page of my website.

I would like to have something dynamic and interesting and utilize the colors in the website - the reds and purples

The business card should be double sided and focus on a unique eye-catching design on the back and include all the relevant company info.

Most importantly, it should say somewhere: "Sign up on our website for a coupon code."

Target Market(s)

Mostly for women gym goers but it shouldn't be too feminine. It should be in keeping with the website design. It should flow and clearly be connected to it

Industry/Entity Type

Business

Contact Information for Business Card

Lorraine K. Vestal
CEO
LVestal@Quorvanexco.com
www.quorvanexco.com
555.417.3820
P.O. Box 47315
Halden, Vermara 00000

Sign up on our website for a coupon code

Font styles to use
Serif
Sans Serif
Other font styles liked:
• Novecento font family and "Quorvanex" is in AR Destine font

Requirements
Must have
• One side should be a bold Quorvanex logo design. Even just the symbol itself may be o.k. (see attached file)

```html
<!DOCTYPE html>
<html lang="en">
<head>
<meta charset="utf-8">
<title>Quorvanex Business Card</title>
<link rel="stylesheet" href="https://fonts.googleapis.com/css2?family=Open+Sans:wght@400;600&display=swap">
<style>
  :root {
    --backdrop: #3a3431;
    --card: #111111;
    --card-edge: #1c1c1c;
    --red: #e0242c;
    --white: #f2f2f2;
    --silver: #c9c9c9;
    --muted: #8d8d8d;
    --divider: #5a1a1c;
  }
  * { margin: 0; padding: 0; box-sizing: border-box; }
  html, body {
    width: 1200px; height: 900px; overflow: hidden;
    background: var(--backdrop);
    font-family: "Open Sans", Arial, sans-serif;
  }
  .canvas {
    position: relative; width: 1200px; height: 900px;
    display: flex; align-items: center; justify-content: center; gap: 40px;
  }
  .card {
    width: 525px; height: 300px;
    background: var(--card);
    border: 1px solid var(--card-edge);
    box-shadow: 0 10px 30px rgba(0,0,0,.45);
    position: relative;
  }

  /* Contact side */
  .contact-side { display: flex; align-items: center; }
  .contact-side .brand-block {
    width: 250px; height: 100%;
    display: flex; align-items: center; justify-content: center; gap: 12px;
  }
  .brand-mark { width: 22px; height: 22px; background: var(--red); flex: none; }
  .brand-name {
    color: var(--white); font-weight: 600; font-size: 26px; letter-spacing: 1px;
  }
  .divider { width: 1px; height: 170px; background: var(--divider); }
  .details { padding-left: 26px; color: var(--white); font-size: 15px; line-height: 1.45; }
  .person-name { color: var(--red); font-size: 19px; text-transform: uppercase; letter-spacing: .5px; }
  .person-title { font-size: 14px; margin-bottom: 8px; }
  .contact-line { display: flex; align-items: center; gap: 8px; }
  .contact-line svg { width: 11px; height: 11px; flex: none; fill: var(--red); }
  .address { margin-top: 10px; }

  /* Logo side */
  .logo-side {
    display: flex; flex-direction: column; align-items: center; justify-content: center;
  }
  .logo-lockup { display: flex; align-items: center; gap: 14px; }
  .logo-lockup .brand-mark { width: 30px; height: 30px; background: var(--silver); }
  .logo-lockup .brand-name { color: var(--silver); font-size: 44px; letter-spacing: 2px; }
  .tagline {
    color: var(--muted); font-size: 13px; letter-spacing: 4px; text-transform: uppercase; margin-top: 4px;
  }
  .coupon-note { color: var(--red); font-size: 14px; margin-top: 12px; }
</style>
</head>
<body>
<main class="canvas">
  <section class="card contact-side">
    <div class="brand-block">
      <span class="brand-mark"></span>
      <span class="brand-name">QUORVANEX</span>
    </div>
    <div class="divider"></div>
    <div class="details">
      <div class="person-name">Lorraine K. Vestal</div>
      <div class="person-title">CEO</div>
      <div class="contact-line">
        <svg viewBox="0 0 24 24"><path d="M6.6 10.8a15 15 0 0 0 6.6 6.6l2.2-2.2a1 1 0 0 1 1-.25 11.4 11.4 0 0 0 3.6.57 1 1 0 0 1 1 1V20a1 1 0 0 1-1 1A17 17 0 0 1 3 4a1 1 0 0 1 1-1h3.5a1 1 0 0 1 1 1c0 1.25.2 2.45.57 3.57a1 1 0 0 1-.25 1z"/></svg>
        <span>555.417.3820</span>
      </div>
      <div class="contact-line">
        <svg viewBox="0 0 24 24"><path d="M2 5h20v14H2z M2 5l10 8 10-8"/></svg>
        <span>LVestal@Quorvanexco.com</span>
      </div>
      <div class="contact-line">
        <svg viewBox="0 0 24 24"><circle cx="12" cy="12" r="10"/></svg>
        <span>www.quorvanexco.com</span>
      </div>
      <div class="address">P.O. Box 47315<br>Halden, Vermara 00000</div>
    </div>
  </section>

  <section class="card logo-side">
    <div class="logo-lockup">
      <span class="brand-mark"></span>
      <span class="brand-name">QUORVANEX</span>
    </div>
    <div class="tagline">Your Training Ally</div>
    <div class="coupon-note">Sign up on our website for a coupon code</div>
  </section>
</main>
</body>
</html>
```